Business card for builder specialising in renovations.

Need a card for our building business. Business name is under Martin Powles.
Have licence number on card ( 527691K)
Contact number (0400 382 415)
Want to work on logo for some business cards and shirts - something with MP or MPB or open to ideas??
No animations, No hammers. Something sharp and eye catching.
Highlight that we are a renovation specialist. Simple on front with extra details on back with some lines to jot down things.

Target Market(s)

Renovators

Industry/Entity Type

Building

Contact Information for Business Card

2 sided with room on back to jot things down.
Extra details on back so front can be simple ..like, renovations, bathrooms, decks, extensions, new builds,

Logo Text

MP

Font styles to use
Serif

Requirements
Must have
• Eye catching design .
• Name : Martin powles
• Licence number
• Contact number - 0400382415
Nice to have
• Some logo design that we can carry through to other forms of advertising
• Local builder
• Quality work
Should not have
• No animations

```html
<!DOCTYPE html>
<html lang="en">
<head>
<meta charset="utf-8">
<title>Martin Powles – Business Card</title>
<link rel="stylesheet" href="https://fonts.googleapis.com/css2?family=Montserrat:wght@600;700&family=Tinos:wght@400;700&display=swap">
<style>
  :root {
    --backdrop: #2c2c2e;
    --brand-blue: #29a9e1;
    --ink: #111111;
    --paper: #ffffff;
    --serif: "Tinos", "Times New Roman", serif;
    --sans: "Montserrat", Arial, sans-serif;
  }
  * { margin: 0; padding: 0; box-sizing: border-box; }
  html, body { width: 1200px; height: 900px; overflow: hidden; }
  body { background: var(--backdrop); position: relative; font-family: var(--serif); }

  .card {
    position: absolute;
    width: 640px;
    height: 370px;
    border-radius: 28px;
    overflow: hidden;
    box-shadow: 0 10px 26px rgba(0,0,0,.45);
  }

  /* Front */
  .card--front { left: 60px; top: 50px; background: var(--brand-blue); }
  .front-mark {
    position: absolute; left: 0; right: 0; top: 48px;
    text-align: center;
    font-family: var(--sans); font-weight: 700;
    font-size: 120px; line-height: 1; letter-spacing: 4px;
    color: var(--paper);
  }
  .front-name {
    position: absolute; left: 0; right: 0; top: 196px;
    text-align: center;
    font-family: var(--sans); font-weight: 600;
    font-size: 30px; letter-spacing: 1px;
    color: var(--paper);
  }
  .front-services {
    position: absolute; left: 50%; top: 252px; transform: translateX(-50%);
    white-space: nowrap;
    border: 1.5px solid var(--ink);
    border-radius: 14px;
    padding: 3px 16px 2px;
    font-size: 15px; letter-spacing: .5px;
    color: var(--paper);
  }
  .front-web {
    position: absolute; left: 0; right: 0; top: 298px;
    text-align: center;
    font-size: 19px; letter-spacing: .5px;
    color: var(--paper);
  }

  /* Back */
  .card--back { left: 500px; top: 470px; background: var(--paper); }
  .back-tab {
    position: absolute; right: 0; top: 28px;
    width: 34px; height: 24px;
    background: var(--brand-blue);
    border-left: 3px solid var(--ink);
  }
  .back-identity {
    position: absolute; right: 46px; top: 24px;
    text-align: right;
  }
  .back-name { font-size: 26px; color: var(--brand-blue); letter-spacing: .5px; line-height: 1.1; }
  .back-role { font-size: 14px; font-weight: 700; color: var(--ink); }

  .rule { position: absolute; height: 1.5px; background: var(--ink); }
  .rule--top { left: 200px; right: 44px; top: 150px; }
  .rule--bottom { left: 200px; right: 44px; top: 318px; }

  .back-mark {
    position: absolute; left: 46px; top: 186px;
    font-family: var(--sans); font-weight: 700;
    font-size: 86px; line-height: 1; letter-spacing: 2px;
    color: var(--ink);
  }

  .contact-list {
    position: absolute; right: 44px; top: 168px;
    list-style: none; text-align: right;
    font-size: 16px; line-height: 24px; color: var(--ink);
  }
  .contact-list li { display: flex; justify-content: flex-end; align-items: center; gap: 8px; }
  .contact-list .icon-slot { width: 14px; height: 14px; display: inline-block; }
  .contact-list svg { width: 14px; height: 14px; display: block; }
  .highlight { color: var(--brand-blue); }
</style>
</head>
<body>

  <section class="card card--front" aria-label="Card front">
    <div class="front-mark">MP</div>
    <div class="front-name">MARTIN POWLES</div>
    <div class="front-services">RENOVATIONS, BATHROOMS, DECKS, EXTENSIONS, NEW BUILDS,</div>
    <div class="front-web">www.powlesbuilding.com</div>
  </section>

  <section class="card card--back" aria-label="Card back">
    <div class="back-tab"></div>
    <div class="back-identity">
      <div class="back-name">MARTIN POWLES</div>
      <div class="back-role">Director</div>
    </div>

    <div class="rule rule--top"></div>

    <div class="back-mark">MP</div>

    <ul class="contact-list">
      <li>Licence: (527691K)<span class="icon-slot"></span></li>
      <li>0400382415
        <svg viewBox="0 0 14 14" aria-hidden="true"><path d="M3 1.5 L5 1.5 L6 4.5 L4.6 5.6 C5.4 7.3 6.7 8.6 8.4 9.4 L9.5 8 L12.5 9 L12.5 11 C12.5 12 11.6 12.6 10.6 12.4 C6 11.6 2.4 8 1.6 3.4 C1.4 2.4 2 1.5 3 1.5 Z" fill="var(--brand-blue)"/></svg>
      </li>
      <li>info@powlesbuilding.com
        <svg viewBox="0 0 14 14" aria-hidden="true"><rect x="1.5" y="3" width="11" height="8" rx="1" fill="none" stroke="var(--brand-blue)" stroke-width="1.4"/><path d="M1.8 3.4 L7 7.6 L12.2 3.4" fill="none" stroke="var(--brand-blue)" stroke-width="1.4"/></svg>
      </li>
      <li>www.<span class="highlight">powlesbuilding</span>.com
        <svg viewBox="0 0 14 14" aria-hidden="true"><circle cx="7" cy="7" r="5.5" fill="none" stroke="var(--brand-blue)" stroke-width="1.3"/><ellipse cx="7" cy="7" rx="2.4" ry="5.5" fill="none" stroke="var(--brand-blue)" stroke-width="1.1"/><path d="M1.5 7 H12.5" stroke="var(--brand-blue)" stroke-width="1.1"/></svg>
      </li>
    </ul>

    <div class="rule rule--bottom"></div>
  </section>

</body>
</html>
```